Designing a front label called Brava Lumo / Bottle Label for a Sparkling Wine called Lumo Brava

We want to bring a Lumo Brava on the market. For this we need a front label. Bottle is painted white and the capsule is fixed. (Black with golden lettering K.Varnholt) Height of label max. 8.5cm. The whole thing should be fresh teen. Happy with reference to Ice .... etc. Secco is the German version of Prosecco. But better. There are currently many Lumo Brava on the market. We also want one now. www.varnholt-kellerei.example We have a nice white lacquered TRV bottle with capsule. it just fehtl the right label. Sender K.Varnholt does not have to be on top ... but if it fits. Lettering is already in the capsule anyway.

Target Market(s)

Supermarket, gals, party, alcohol, RRP 4.99 €

Font styles to use
Decorative

Colors

Designer to choose colors to be used in the design.

Requirements
Must have
• Self-adhesive label, printable data in 4c, reference to ice, black, golden reference to the capsule.
Nice to have
• Ice cubes, cool, cool.
Should not have
• boredom

```html
<!DOCTYPE html>
<html lang="en">
<head>
<meta charset="utf-8">
<title>Lumo Brava Ice – Front Label</title>
<link rel="stylesheet" href="https://fonts.googleapis.com/css2?family=Great+Vibes&family=Crimson+Text:wght@400&display=swap">
<style>
  :root {
    --label-black: #000000;
    --gold-light: #f8dc8c;
    --gold-mid: #e2b04a;
    --gold-deep: #b8861f;
    --ink: #0d0a05;
    --script: "Great Vibes", cursive;
    --serif: "Crimson Text", serif;
  }
  html, body {
    margin: 0;
    padding: 0;
    overflow: hidden;
    background: var(--label-black);
  }
  .label {
    position: relative;
    width: 896px;
    height: 1200px;
    background: var(--label-black);
    overflow: hidden;
  }
  .label-art {
    position: absolute;
    inset: 0;
  }
  .house-name {
    position: absolute;
    top: 84px;
    left: 0;
    width: 100%;
    margin: 0;
    text-align: center;
    font-family: var(--script);
    font-size: 76px;
    line-height: 1;
    color: var(--gold-mid);
  }
  .house-mark {
    position: absolute;
    top: 170px;
    left: 358px;
    width: 180px;
    height: 140px;
    display: flex;
    flex-direction: column;
    align-items: center;
    gap: 8px;
  }
  .house-mark-dot {
    width: 84px;
    height: 84px;
    border-radius: 50%;
    background: var(--gold-mid);
  }
  .house-mark-name {
    font-family: var(--script);
    font-size: 34px;
    line-height: 1;
    color: var(--gold-mid);
  }
  .product-name {
    position: absolute;
    top: 420px;
    left: 155px;
    width: 586px;
    margin: 0;
    text-align: center;
    font-family: var(--script);
    font-weight: 400;
    color: var(--ink);
  }
  .product-name .product-brand {
    display: block;
    font-size: 124px;
    line-height: 170px;
    white-space: nowrap;
  }
  .product-name .product-ice {
    display: block;
    font-size: 210px;
    line-height: 220px;
  }
  .wine-type {
    position: absolute;
    top: 892px;
    left: 0;
    width: 100%;
    margin: 0;
    text-align: center;
    font-family: var(--script);
    font-size: 62px;
    line-height: 1;
    word-spacing: 14px;
    color: var(--ink);
  }
  .net-content {
    position: absolute;
    top: 1082px;
    left: 0;
    width: 100%;
    margin: 0;
    text-align: center;
    font-family: var(--serif);
    font-size: 37px;
    color: var(--gold-mid);
  }
</style>
</head>
<body>
<main class="label">
  <svg class="label-art" width="896" height="1200" viewBox="0 0 896 1200">
    <defs>
      <linearGradient id="shieldGold" x1="0" y1="0" x2="1" y2="1">
        <stop offset="0" stop-color="#f3cf73"/>
        <stop offset="0.35" stop-color="#d9a537"/>
        <stop offset="0.6" stop-color="#f8dc8c"/>
        <stop offset="1" stop-color="#c8952c"/>
      </linearGradient>
      <linearGradient id="ribbonGold" x1="0" y1="0" x2="0" y2="1">
        <stop offset="0" stop-color="#f6d98e"/>
        <stop offset="0.5" stop-color="#e8bf63"/>
        <stop offset="1" stop-color="#c99434"/>
      </linearGradient>
      <linearGradient id="ribbonFold" x1="0" y1="0" x2="1" y2="0">
        <stop offset="0" stop-color="#5e3d16"/>
        <stop offset="1" stop-color="#a5762c"/>
      </linearGradient>
      <radialGradient id="ornamentGold" cx="0.5" cy="0.5" r="0.6">
        <stop offset="0" stop-color="#e8bb55" stop-opacity="0.55"/>
        <stop offset="1" stop-color="#b8861f" stop-opacity="0.15"/>
      </radialGradient>
    </defs>

    <g class="corner-flourishes">
      <path role="img" aria-label="Gold baroque flourish, top left corner" d="M8 8 H250 Q120 40 70 100 Q40 160 40 260 H8 Z" fill="url(#ornamentGold)"/>
      <path role="img" aria-label="Gold baroque flourish, top right corner" d="M888 8 H646 Q776 40 826 100 Q856 160 856 260 H888 Z" fill="url(#ornamentGold)"/>
      <path role="img" aria-label="Gold baroque flourish, bottom left corner" d="M8 1192 H250 Q120 1160 70 1100 Q40 1040 40 940 H8 Z" fill="url(#ornamentGold)"/>
      <path role="img" aria-label="Gold baroque flourish, bottom right corner" d="M888 1192 H646 Q776 1160 826 1100 Q856 1040 856 940 H888 Z" fill="url(#ornamentGold)"/>
    </g>

    <g class="side-rules" stroke="#e2b04a" stroke-width="3">
      <line x1="36" y1="270" x2="36" y2="980"/>
      <line x1="860" y1="270" x2="860" y2="980"/>
    </g>
    <g class="side-ornaments">
      <rect role="img" aria-label="Gold scroll ornament on left rule" x="12" y="540" width="48" height="110" rx="24" fill="url(#ornamentGold)"/>
      <rect role="img" aria-label="Gold scroll ornament on right rule" x="836" y="540" width="48" height="110" rx="24" fill="url(#ornamentGold)"/>
    </g>

    <path class="shield" d="M155 378 Q250 400 330 372 Q400 346 448 380 Q496 346 566 372 Q646 400 741 378 L741 640 Q741 800 448 900 Q155 800 155 640 Z" fill="url(#shieldGold)"/>

    <g class="ribbon">
      <path d="M48 762 Q140 748 206 786 L230 920 Q150 880 62 900 L100 830 Z" fill="url(#ribbonGold)"/>
      <path d="M848 762 Q756 748 690 786 L666 920 Q746 880 834 900 L796 830 Z" fill="url(#ribbonGold)"/>
      <path d="M160 800 L250 868 L250 920 L176 900 Z" fill="url(#ribbonFold)"/>
      <path d="M736 800 L646 868 L646 920 L720 900 Z" fill="url(#ribbonFold)"/>
      <path d="M218 868 Q448 830 678 868 L678 986 Q448 950 218 986 Z" fill="url(#ribbonGold)"/>
    </g>
  </svg>

  <p class="house-name">K.Varnholt</p>
  <div class="house-mark">
    <span class="house-mark-dot"></span>
    <span class="house-mark-name">K.Varnholt</span>
  </div>

  <h1 class="product-name">
    <span class="product-brand">Lumo Brava</span>
    <span class="product-ice">Ice</span>
  </h1>
  <p class="wine-type">Sparkling Wine</p>
  <p class="net-content">Net wt.1fl oz</p>
</main>
</body>
</html>
```